Stonebridge Building and Projects business cards

A business card with watermark background (construction work)

Company logo attached

Home improvement projects
House renovations
Bathroom and kitchen renovations
House extensions
New builds and granny flats

Director Omar Haddani
(Phone number)
omar@sbpbuilding.com.au
(Instagram logo) sbp_building

```html
<!DOCTYPE html>
<html lang="en">
<head>
<meta charset="utf-8">
<title>Stonebridge Building and Projects – Business Cards</title>
<link href="https://fonts.googleapis.com/css2?family=Roboto:wght@400;500;700&display=swap" rel="stylesheet">
<style>
  :root {
    --brand-blue: #1a74bd;
    --ink-dark: #3a3d42;
    --ink-mid: #55585d;
    --card-white: #f7f7f6;
    --page-bg: #e6e6e4;
    --swoosh-grey: #45484d;
  }
  * { box-sizing: border-box; margin: 0; padding: 0; }
  html, body { width: 1200px; height: 1050px; overflow: hidden; }
  body {
    background: var(--page-bg);
    font-family: "Roboto", Arial, sans-serif;
    position: relative;
  }
  .card {
    position: absolute;
    width: 560px;
    height: 320px;
    border-radius: 18px;
    background: var(--card-white);
    overflow: hidden;
    box-shadow: 0 6px 18px rgba(0,0,0,0.18);
  }
  .card--services { left: 320px; top: 150px; }
  .card--contact { left: 320px; top: 570px; }

  .company-name {
    position: absolute;
    color: var(--brand-blue);
    font-weight: 700;
    font-size: 27px;
    line-height: 1.08;
    display: flex;
    align-items: flex-start;
    gap: 10px;
  }
  .company-name__mark {
    width: 14px; height: 14px;
    background: var(--brand-blue);
    margin-top: 7px;
    flex: none;
  }
  .card--services .company-name { left: 34px; top: 150px; width: 240px; }
  .card--contact .company-name { left: 34px; top: 190px; width: 260px; }

  .service-list {
    position: absolute;
    left: 296px;
    top: 58px;
    list-style: none;
    color: var(--ink-dark);
    font-size: 14.5px;
    line-height: 23px;
  }
  .service-list li { position: relative; padding-left: 20px; }
  .service-list li::before {
    content: "";
    position: absolute;
    left: 0; top: 8px;
    width: 7px; height: 7px;
    background: var(--brand-blue);
  }
  .service-list .continued { padding-left: 20px; }
  .service-list .continued::before { display: none; }

  .social-band {
    position: absolute;
    right: 0; bottom: 0;
    width: 300px; height: 62px;
    background: var(--brand-blue);
    border-top-left-radius: 22px;
    color: #fff;
    font-size: 14px;
    display: flex;
    align-items: center;
    padding-left: 36px;
    gap: 9px;
  }
  .social-dot {
    width: 13px; height: 13px;
    border: 2px solid #fff;
    border-radius: 50%;
  }

  .wave { position: absolute; inset: 0; }
  .holder {
    position: absolute;
    right: 40px; top: 28px;
    text-align: right;
    color: #fff;
  }
  .holder__name { font-size: 25px; font-weight: 700; }
  .holder__role { font-size: 13px; margin-top: 2px; }

  .contact-list {
    position: absolute;
    right: 32px; top: 170px;
    list-style: none;
    color: var(--ink-dark);
    font-size: 14px;
    line-height: 22px;
    text-align: right;
  }
  .contact-list li { display: flex; align-items: center; justify-content: flex-end; gap: 9px; }
  .contact-list svg { width: 14px; height: 14px; flex: none; }
</style>
</head>
<body>

  <section class="card card--services" aria-label="Business card front, services">
    <div class="company-name"><span class="company-name__mark"></span><span>Stonebridge Building and Projects</span></div>
    <ul class="service-list">
      <li>Home improvement projects</li>
      <li>House renovations</li>
      <li>Bathroom and kitchen</li>
      <li class="continued">renovations</li>
      <li>House extensions</li>
      <li>New builds and granny flats</li>
    </ul>
    <div class="social-band"><span class="social-dot"></span><span>sbp_building</span></div>
  </section>

  <section class="card card--contact" aria-label="Business card back, contact details">
    <svg class="wave" viewBox="0 0 560 320" aria-hidden="true">
      <path d="M0 0 H560 V45 C500 95 400 108 290 114 C170 120 70 108 0 100 Z" fill="var(--brand-blue)"/>
      <path d="M0 128 C90 118 190 126 300 122 C410 118 500 100 560 62 V76 C500 116 410 134 300 136 C190 138 90 130 0 142 Z" fill="var(--swoosh-grey)"/>
    </svg>
    <div class="holder">
      <div class="holder__name">Omar Haddani</div>
      <div class="holder__role">Managing Director</div>
    </div>
    <div class="company-name"><span class="company-name__mark"></span><span>Stonebridge Building and Projects</span></div>
    <ul class="contact-list">
      <li>0400 318 527
        <svg viewBox="0 0 14 14"><circle cx="7" cy="7" r="6.2" fill="none" stroke="var(--brand-blue)" stroke-width="1.4"/><path d="M4.5 4 L6 3.8 L6.6 5.6 L5.8 6.3 C6.3 7.3 6.9 7.9 7.8 8.3 L8.5 7.5 L10.2 8.1 L10 9.6 C7 9.8 4.3 7 4.5 4 Z" fill="var(--brand-blue)"/></svg></li>
      <li>sbpbuilding.com.au
        <svg viewBox="0 0 14 14"><rect x="1" y="3" width="12" height="8.5" rx="1" fill="none" stroke="var(--brand-blue)" stroke-width="1.4"/><path d="M1.5 3.6 L7 8 L12.5 3.6" fill="none" stroke="var(--brand-blue)" stroke-width="1.3"/></svg></li>
      <li>sbp_building
        <svg viewBox="0 0 14 14"><circle cx="7" cy="7" r="6" fill="none" stroke="var(--brand-blue)" stroke-width="1.4"/><ellipse cx="7" cy="7" rx="2.6" ry="6" fill="none" stroke="var(--brand-blue)" stroke-width="1.1"/><path d="M1 7 H13" stroke="var(--brand-blue)" stroke-width="1.1"/></svg></li>
      <li>omar@sbpbuilding.com.au
        <svg viewBox="0 0 14 14"><circle cx="7" cy="7" r="5.5" fill="none" stroke="var(--brand-blue)" stroke-width="1.6"/></svg></li>
    </ul>
  </section>

</body>
</html>
```